Book Title: Quiet Harbors -- Notes From a Restless Pulpit Today

I am looking for just the book cover design, do not need spine or back cover art.

This book is a memoir and the cover needs to be prepared for print and ebook applications.

The part of the title that follows the dash ("Notes From a Restless Pulpit Today") is not a subtitle but a tag and can be separated from the title itself.

I am inclined to a traditional design with "modern and minimalist" tendencies. I like graphic images that convey the idea of a "journey" or "quest". The memoir is about my pastoral work as a Christian minister but it is not a "religious" book. I do not want churches or any traditional religious symbols on the cover. In fact this book is directed toward those who have little, if any, interest in organized religion of any kind and if that could somehow be captured in the cover art it would be useful.

I am attaching a file with some sample cover art designs that I like or do not like to help guide your thinking. I am open to your interpretation and creative thinking. This book is a labor of love and I want the cover art to reflect my deep thinking on the topic.

```html
<!DOCTYPE html>
<html lang="en">
<head>
<meta charset="UTF-8">
<title>Quiet Harbors — Book Cover</title>
<link rel="stylesheet" href="https://fonts.googleapis.com/css2?family=Cinzel:wght@400;500&family=Montserrat:wght@600&display=swap">
<style>
  :root {
    --paper: #f5f7f6;
    --title-olive: #605a40;
    --tag-slate: #5a7078;
    --sky-teal: #66a6bc;
    --shore-teal: #2a6570;
    --water-teal: #3a8aa0;
  }
  * { margin: 0; padding: 0; box-sizing: border-box; }
  html, body {
    width: 800px;
    height: 1200px;
    overflow: hidden;
    background: var(--paper);
  }
  .cover {
    position: relative;
    width: 800px;
    height: 1200px;
    background: var(--paper);
  }
  .title {
    position: absolute;
    left: 0;
    width: 800px;
    text-align: center;
    font-family: "Cinzel", serif;
    font-weight: 500;
    color: var(--title-olive);
    line-height: 1;
  }
  .title-line-one {
    top: 52px;
    font-size: 92px;
    letter-spacing: 0.3em;
    padding-left: 0.3em;
  }
  .title-line-two {
    top: 156px;
    font-size: 112px;
    letter-spacing: 0.1em;
    padding-left: 0.1em;
  }
  .tagline {
    position: absolute;
    top: 314px;
    left: 0;
    width: 800px;
    text-align: center;
    font-family: "Cinzel", serif;
    font-weight: 400;
    font-size: 36px;
    line-height: 35px;
    letter-spacing: 0.14em;
    color: var(--tag-slate);
  }
  .scene {
    position: absolute;
    top: 428px;
    left: 0;
    width: 800px;
    height: 687px;
    background: linear-gradient(
      to bottom,
      var(--paper) 0%,
      var(--sky-teal) 12%,
      var(--sky-teal) 48%,
      var(--shore-teal) 56%,
      var(--shore-teal) 60%,
      var(--water-teal) 64%,
      var(--water-teal) 100%
    );
  }
  .author {
    position: absolute;
    top: 1138px;
    left: 0;
    width: 800px;
    text-align: center;
    font-family: "Montserrat", sans-serif;
    font-weight: 600;
    font-size: 31px;
    line-height: 1;
    letter-spacing: 0.42em;
    padding-left: 0.42em;
    color: var(--tag-slate);
  }
</style>
</head>
<body>
  <main class="cover">
    <h1>
      <span class="title title-line-one">QUIET</span>
      <span class="title title-line-two">HARBORS</span>
    </h1>
    <p class="tagline">NOTES FROM A RESTLESS<br>PULPIT TODAY</p>
    <div class="scene" role="img" aria-label="Posterized teal illustration of a white sailboat gliding on a calm lake, with a wooded shoreline and hazy sky behind it"></div>
    <p class="author">AUTHOR NAME</p>
  </main>
</body>
</html>
```